Velora Entertainment

Logo for business card design

Target Market(s)

potential film investors and screenwriters

Industry/Entity Type

Business

Contact Information for Business Card

as shown, website here is a placeholder position

Requirements
Must have
• great visual appeal
Nice to have
• harmony of colors; must evoke spirit of
• U.S.-China cooperation

```html
<!DOCTYPE html>
<html lang="en">
<head>
<meta charset="utf-8">
<title>Velora Entertainment – Business Card</title>
<link href="https://fonts.googleapis.com/css2?family=Open+Sans:wght@400;600;700&display=swap" rel="stylesheet">
<style>
  :root {
    --red: #e30613;
    --yellow: #ffde00;
    --navy: #1b1f86;
    --ink: #222222;
    --paper: #ffffff;
    --band: #9a9a9a;
    --backdrop: #3d3d3d;
  }
  * { margin: 0; padding: 0; box-sizing: border-box; }
  html, body {
    width: 1105px; height: 1200px; overflow: hidden;
    background: var(--backdrop);
    font-family: "Open Sans", Arial, sans-serif;
  }
  .card {
    position: absolute; left: 72px; top: 326px;
    width: 960px; height: 548px;
    background: var(--paper);
  }
  .stripe { position: absolute; top: 0; height: 15px; }
  .stripe--red { left: 0; width: 316px; background: var(--red); }
  .stripe--yellow { left: 320px; width: 318px; background: var(--yellow); }
  .stripe--navy { left: 642px; width: 318px; background: var(--navy); }
  .base-band { position: absolute; left: 0; bottom: 0; width: 100%; height: 18px; background: var(--band); }

  .brand {
    position: absolute; left: 90px; top: 256px;
    display: flex; align-items: center; gap: 14px;
  }
  .brand__square { width: 40px; height: 40px; background: var(--red); }
  .brand__name {
    font-weight: 700; font-size: 26px; color: var(--navy);
    white-space: nowrap;
  }

  .divider {
    position: absolute; left: 498px; top: 120px;
    width: 2px; height: 340px;
    background: linear-gradient(to bottom, rgba(150,150,150,0), #9a9a9a 20%, #9a9a9a 80%, rgba(150,150,150,0));
  }

  .contact { position: absolute; left: 548px; top: 118px; color: var(--ink); }
  .contact__name { font-weight: 600; font-size: 32px; color: var(--red); line-height: 1.15; }
  .contact__title { font-size: 27px; color: var(--navy); line-height: 1.3; }
  .contact__address { margin-top: 20px; font-size: 26px; line-height: 1.4; }
  .contact__list { list-style: none; margin-top: 12px; font-size: 26px; line-height: 1.4; }
  .contact__item { display: flex; align-items: center; gap: 14px; }
  .contact__icon { width: 24px; height: 24px; flex: none; fill: var(--red); }
</style>
</head>
<body>
  <div class="card">
    <div class="stripe stripe--red"></div>
    <div class="stripe stripe--yellow"></div>
    <div class="stripe stripe--navy"></div>

    <div class="brand">
      <div class="brand__square"></div>
      <span class="brand__name">Velora Entertainment</span>
    </div>

    <div class="divider"></div>

    <div class="contact">
      <p class="contact__name">Daniel Hart</p>
      <p class="contact__title">CEO/Founder</p>
      <p class="contact__address">4120 Maple Crest Road<br>Riverton, Oregon 97201</p>
      <ul class="contact__list">
        <li class="contact__item">
          <svg class="contact__icon" viewBox="0 0 24 24" aria-hidden="true"><path d="M6.6 2.5l3 3.6-1.8 2.4c1.3 2.9 3.6 5.2 6.5 6.6l2.4-1.8 3.6 3-1.6 3.6C10.6 19.6 4.4 13.4 3 5.1z"/></svg>
          <span>555 214 7730</span>
        </li>
        <li class="contact__item">
          <svg class="contact__icon" viewBox="0 0 24 24" aria-hidden="true"><path d="M7 1h10a2 2 0 012 2v18a2 2 0 01-2 2H7a2 2 0 01-2-2V3a2 2 0 012-2zm0 3v14h10V4zm5 15.5a1 1 0 100 2 1 1 0 000-2z"/></svg>
          <span>555 382 6419</span>
        </li>
        <li class="contact__item">
          <svg class="contact__icon" viewBox="0 0 24 24" aria-hidden="true"><path d="M2 6h20v12H2zm2 1.5l8 6 8-6z" fill-rule="evenodd"/></svg>
          <span>hello@velorafilms.com</span>
        </li>
        <li class="contact__item">
          <svg class="contact__icon" viewBox="0 0 24 24" aria-hidden="true"><circle cx="12" cy="12" r="10"/><path d="M2 12h20M12 2c3 3 3 17 0 20M12 2c-3 3-3 17 0 20" stroke="#fff" stroke-width="1.4" fill="none"/></svg>
          <span>www.velorafilms.com</span>
        </li>
      </ul>
    </div>

    <div class="base-band"></div>
  </div>
</body>
</html>
```